Magento e-commerce webdesign

We need a full e-commerce design for a company based in France. The website will sell belts (men / women).
In files, you have our logo. We made a try for a brown visit card, but it's just an idea. The brown color can be used if it looks like leather, warning it MUSN'T look like "brown shit" :)
So you are free with color but never forget we sell belts and it's both for men & women (upmarket). You can make your own colors changes on the logo (only colors).
You'll find 2 wireframes with the home page & the category page. Elements are in french. UPDATED : you have a traduction files, but it would better if you can make it in french.
Photos have to be on a white background.
Carroussel & every pictures of the wireframes area are very importants.
Target Market(s)
Men & women
Fashion peoples
Upmarket
Industry/Entity Type
It Company
Requirements
Must have
- work on the colors
- work on the pictures (carroussel, newsletter, ventes privées, services, category)
- pro & upmarket
Nice to have
- Product detail page
- Texts in french
Should not have
- Shitty brown colors

```html
<!DOCTYPE html>
<html lang="fr">
<head>
<meta charset="utf-8">
<title>Sanglio — Ceintures homme &amp; femme</title>
<link href="https://fonts.googleapis.com/css2?family=Didact+Gothic&family=Arimo:wght@400;700&display=swap" rel="stylesheet">
<style>
:root{
  --leather-dark:#3b2116;
  --leather:#5e3a2a;
  --leather-light:#7a5140;
  --panel-brown:#3a2218;
  --ribbon:#8a5538;
  --cream:#f1e0d4;
  --line:#d8a886;
  --text-light:#f3e9e2;
  --text-muted:#c9b2a6;
  --text-dark:#333;
  --pink:#e4468f;
  --white:#fff;
}
*{box-sizing:border-box;margin:0;padding:0}
html,body{width:1200px;height:1131px;overflow:hidden}
body{position:relative;background:#fff;font-family:"Arimo",Arial,sans-serif;color:var(--text-dark)}
.abs{position:absolute}
.heading{font-family:"Didact Gothic","Trebuchet MS",sans-serif;font-weight:400}

.topline{left:0;top:0;width:1200px;height:8px;background:#111}
.header{left:0;top:8px;width:1200px;height:137px;background:radial-gradient(ellipse at 50% 30%,var(--leather-light),var(--leather) 55%,var(--leather-dark))}
.nav{left:0;top:145px;width:1200px;height:34px;background:linear-gradient(#6b4231,#4e2f22);box-shadow:0 2px 3px rgba(0,0,0,.35)}
.brand{left:119px;top:30px;color:#e9ddd5}
.brand-mark{width:22px;height:22px;border:2px solid #e9ddd5;border-radius:50%;margin-left:66px;margin-bottom:4px}
.brand-name{font-family:"Didact Gothic",sans-serif;font-size:30px;letter-spacing:1px;line-height:36px}
.brand-url{font-size:10px;letter-spacing:2.5px;color:#cdb8ab}

.util{color:var(--text-light);font-weight:700;font-size:14px;display:flex;align-items:center;gap:8px}
.util svg{fill:#ddd}
.util-rule{left:722px;top:74px;width:336px;height:1px;background:rgba(255,255,255,.3)}
.cart-state{left:858px;top:80px;color:#fff;font-size:11px;font-weight:700}
.phones{left:916px;top:79px;color:#fff;font-size:12.5px;font-weight:700;line-height:14px;letter-spacing:.5px}

.nav-item{top:151px;color:#f5ece6;font-size:19px;line-height:22px;text-shadow:0 1px 1px #000}
.nav-sep{top:146px;width:1px;height:31px;background:rgba(255,255,255,.2)}

.content{left:102px;top:179px;width:972px;height:693px;background:#fff;box-shadow:0 0 3px rgba(0,0,0,.35)}

.hero{left:112px;top:191px;width:651px;height:277px;border:1px solid var(--line);background:linear-gradient(90deg,#e2c2ad 0%,#f4e8e0 45%,#fff 70%)}
.hero-belts,.hero-person{position:absolute;border-radius:6px}
.hero-belts{left:28px;top:20px;width:350px;height:235px;background:radial-gradient(ellipse,#6e4a34,#8a6650 55%,transparent 75%)}
.hero-person{left:400px;top:2px;width:240px;height:270px;background:radial-gradient(ellipse at 55% 40%,#e8d6cc,#c5d3e6 45%,transparent 72%)}
.btn-products{left:466px;top:228px;width:168px;height:38px;border-radius:5px;background:linear-gradient(#f06aa9,var(--pink));color:#fff;font-size:19px;display:flex;align-items:center;justify-content:center;gap:10px;box-shadow:0 0 0 2px #fff}

.promo{left:773px;width:285px;height:89px;background:var(--panel-brown);border:3px solid #4a2e22;overflow:hidden}
.promo h2{position:absolute;left:17px;top:9px;color:#f4ece6;font-size:27px;line-height:32px;white-space:nowrap}
.promo p{position:absolute;left:19px;top:46px;color:#cdbfb7;font-size:12px;line-height:14px}
.promo .ribbon{position:absolute;right:6px;top:6px;width:58px;height:74px;background:linear-gradient(160deg,#a06a4a,var(--ribbon))}
.promo .ribbon span{position:absolute;left:2px;top:32px;transform:rotate(-58deg);font-size:11px;color:#f0e1d6;white-space:nowrap}

.carousel{left:112px;top:476px;width:950px;height:258px;border:1px solid var(--line)}
.card{top:483px;width:180px;height:247px;background:var(--cream);border-radius:4px}
.card .photo{position:absolute;left:4px;top:4px;width:172px;height:174px;background:#fff;border-radius:3px}
.card .photo i{position:absolute;left:22px;top:30px;width:128px;height:116px;border-radius:40%}
.card p{position:absolute;left:18px;top:185px;width:150px;font-size:9.5px;line-height:12px;color:#222}
.card .price{position:absolute;left:10px;top:226px;font-size:14px;color:#444}
.card .buy{position:absolute;right:0;bottom:3px;width:70px;height:22px;background:linear-gradient(#5a3222,#3c1f15);color:#fff;font-size:11px;font-weight:700;display:flex;align-items:center;justify-content:center;border-radius:3px 0 3px 0}
.arrow{top:559px;width:48px;height:48px;border-radius:50%;background:#fff;box-shadow:0 0 4px rgba(0,0,0,.3);display:flex;align-items:center;justify-content:center}

.trust{left:112px;top:758px;width:950px;height:77px;border:1px solid #ddd;background:repeating-linear-gradient(135deg,#f2f2f2 0 2px,#e9e9e9 2px 4px)}
.trust-item{font-size:12px;color:#444;line-height:17px}
.trust-item small{display:block;font-size:9.5px;line-height:11px}
.card-shape{position:absolute;top:0;width:34px;height:22px;border:2px solid #222;border-radius:2px}

.footer{left:0;top:877px;width:1200px;height:254px;background:radial-gradient(ellipse at 40% 40%,#6a4333,var(--leather) 50%,var(--leather-dark))}
.blog{left:107px;top:902px;width:577px;height:206px;background:rgba(255,255,255,.1);border-radius:12px}
.blog h2{position:absolute;left:18px;top:8px;color:#f5ece6;font-size:29px;line-height:34px}
.blog .rule{position:absolute;left:18px;top:42px;width:540px;height:1px;background:rgba(255,255,255,.3)}
.blog p{position:absolute;left:18px;width:530px;color:var(--text-muted);font-size:12px;line-height:14.5px}
.blog .sig{position:absolute;right:26px;bottom:6px;color:#e7dcd5;font-family:"Didact Gothic",sans-serif;font-size:18px}
.share{left:723px;top:910px;color:#f5ece6;font-size:29px;line-height:34px}
.social{top:950px;width:72px;height:72px;border-radius:50%;background:radial-gradient(circle at 40% 35%,#5ba4dd,#1f5e9b);border:4px solid #e8e8e8}
.links{left:723px;top:1038px;width:278px;height:67px;background:rgba(255,255,255,.12);border-radius:6px;padding:12px 12px;color:#f2e9e3;font-size:19px;line-height:25px}
.links span{margin-right:26px}
</style>
</head>
<body>
<div class="abs topline"></div>
<header class="abs header"></header>
<div class="abs brand">
  <div class="brand-mark"></div>
  <div class="brand-name">Sanglio</div>
  <div class="brand-url">www.sanglio-boutique.fr</div>
</div>

<div class="abs util" style="left:750px;top:44px">
  <svg width="32" height="22" viewBox="0 0 32 22"><path d="M0 2h6l4 12h16l4-10H9" stroke="#ddd" stroke-width="2" fill="none"/><circle cx="12" cy="19" r="2"/><circle cx="24" cy="19" r="2"/></svg>Panier
</div>
<div class="abs util" style="left:898px;top:44px">
  <svg width="16" height="22" viewBox="0 0 16 22"><path d="M4 1l4 5-2 3c1 3 3 6 5 7l3-2 2 5-3 2C6 20 1 10 2 3z"/></svg>Service Clients
</div>
<div class="abs util-rule"></div>
<div class="abs cart-state">(vide)</div>
<div class="abs phones">+33 (0)1 45 00 12 30<br>+32 (0)2 00 51 789</div>

<nav class="abs nav"></nav>
<div class="abs nav-item heading" style="left:121px">Homme</div>
<div class="abs nav-sep" style="left:218px"></div>
<div class="abs nav-item heading" style="left:245px">Femme</div>
<div class="abs nav-sep" style="left:337px"></div>
<div class="abs nav-item heading" style="left:353px">Accessories</div>
<div class="abs nav-item heading" style="left:818px">Mon Compte</div>
<div class="abs nav-item heading" style="left:965px">Parrainage</div>

<main class="abs content"></main>

<section class="abs hero">
  <div class="hero-belts" role="img" aria-label="Photo de ceintures en cuir ornées de boucles"></div>
  <div class="hero-person" role="img" aria-label="Photo d'une conseillère au téléphone qui montre les produits"></div>
  <div class="abs btn-products heading">View Products
    <svg width="10" height="14" viewBox="0 0 10 14"><path d="M0 0l10 7-10 7z" fill="#fff"/></svg></div>
</section>

<div class="abs promo" style="top:190px"><h2 class="heading">Newsletter</h2><p>Tease of Transfix sheets containing<br>Lorem Ipsum passages.</p><div class="ribbon"><span>Read More..</span></div></div>
<div class="abs promo" style="top:285px"><h2 class="heading">Ventess Privess</h2><p>Tease of Transfix sheets containing<br>Lorem Ipsum passages.</p><div class="ribbon"><span>Read More..</span></div></div>
<div class="abs promo" style="top:379px"><h2 class="heading">Services</h2><p>Tease of Transfix sheets containing<br>Lorem Ipsum passages.</p><div class="ribbon"><span>Read More..</span></div></div>

<section class="abs carousel"></section>
<div class="abs card" style="left:118px"><div class="photo"><i role="img" aria-label="Ceinture zébrée noir et blanc" style="background:radial-gradient(#999,#ddd 60%,transparent 72%)"></i></div><p>Lorem Ipsum is simply dummy text of the printing and typesetting industry.</p><div class="price">$ 420.00</div><div class="buy">Buy Now</div></div>
<div class="abs card" style="left:307px"><div class="photo"><i role="img" aria-label="Ceinture en cuir marron enroulée" style="background:radial-gradient(#6a4030,#8a5a44 55%,transparent 72%)"></i></div><p>Lorem Ipsum is simply dummy text of the printing and typesetting industry.</p><div class="price">$ 420.00</div><div class="buy">Buy Now</div></div>
<div class="abs card" style="left:497px"><div class="photo"><i role="img" aria-label="Ceinture violette à boucle strass" style="background:radial-gradient(#7a5ab0,#5a3a85 55%,transparent 72%)"></i></div><p>Lorem Ipsum is simply dummy text of the printing and typesetting industry.</p><div class="price">$ 420.00</div><div class="buy">Buy Now</div></div>
<div class="abs card" style="left:687px"><div class="photo"><i role="img" aria-label="Ceinture tressée noire" style="background:radial-gradient(#444,#777 55%,transparent 72%)"></i></div><p>Lorem Ipsum is simply dummy text of the printing and typesetting industry.</p><div class="price">$ 420.00</div><div class="buy">Buy Now</div></div>
<div class="abs card" style="left:877px"><div class="photo"><i role="img" aria-label="Ceinture violette à boucle strass" style="background:radial-gradient(#7a5ab0,#5a3a85 55%,transparent 72%)"></i></div><p>Lorem Ipsum is simply dummy text of the printing and typesetting industry.</p><div class="price">$ 420.00</div><div class="buy">Buy Now</div></div>
<div class="abs arrow" style="left:94px"><svg width="12" height="14" viewBox="0 0 12 14"><path d="M9 1L3 7l6 6" stroke="#222" stroke-width="3" fill="none"/></svg></div>
<div class="abs arrow" style="left:1034px"><svg width="12" height="14" viewBox="0 0 12 14"><path d="M3 1l6 6-6 6" stroke="#222" stroke-width="3" fill="none"/></svg></div>

<section class="abs trust"></section>
<div class="abs trust-item" style="left:132px;top:784px;width:230px;height:24px">
  <div class="card-shape" style="left:0;background:#2a8a8a"></div>
  <div class="card-shape" style="left:37px;background:#c0502a"></div>
  <div class="card-shape" style="left:74px;background:#2a4f9a"></div>
  <span style="position:absolute;left:120px;top:4px">Paiement sécurisé</span>
</div>
<div class="abs trust-item" style="left:388px;top:776px">
  <svg class="abs" style="left:0;top:0" width="34" height="42" viewBox="0 0 34 42"><circle cx="17" cy="21" r="15" fill="#f6a53a"/></svg>
  <div style="margin-left:40px">Livraison<small>du lundi au vendredi de 9h30 à 19h30</small></div>
</div>
<div class="abs trust-item" style="left:650px;top:780px">
  <svg class="abs" style="left:0;top:0" width="22" height="34" viewBox="0 0 22 34"><path d="M6 1l6 7-3 4c2 5 4 9 8 11l3-3 3 7-4 4C7 30 0 16 2 4z" fill="#999"/></svg>
  <div style="margin-left:32px">Service Client<br>Email</div>
</div>
<div class="abs trust-item" style="left:810px;top:770px">
  <svg class="abs" style="left:0;top:0" width="44" height="56" viewBox="0 0 44 56"><path d="M12 34l-6 20 10-6 6 8 4-22z" fill="#b5121b"/><circle cx="22" cy="22" r="20" fill="#cc1a22"/></svg>
  <div style="margin-left:54px;margin-top:10px">Grantie<small>du lundi au vendredi de 9h30 à 19h30</small></div>
</div>

<footer class="abs footer"></footer>
<section class="abs blog">
  <h2 class="heading">Derniers articles du blog</h2>
  <div class="rule"></div>
  <p style="top:52px">Lorem Ipsum is simply dummy text of the printing and typesetting industry. Lorem Ipsum has been the industry's standard dummy text ever since the 1500s, when an unknown printer took a galley of type and scrambled it to make a type specimen book. It has survived not only five centuries, but also the leap into electronic typesetting, remaining essentially unchanged.</p>
  <p style="top:124px">It was popularised in the 1960s with the release of Transfix sheets containing Lorem Ipsum passages, and more recently with desktop publishing software like Mise en Page Studio including versions of Lorem Ipsum.</p>
  <div class="sig">Sanglio</div>
</section>
<div class="abs share heading">Partager</div>
<div class="abs social" style="left:724px" role="img" aria-label="Partager sur un réseau social"></div>
<div class="abs social" style="left:812px" role="img" aria-label="Partager sur un réseau social"></div>
<div class="abs links heading"><span>CGV</span><span>CGU</span><span>Plan Du Site</span><br>Credits</div>
</body>
</html>
```